Business card for marketing analytics company

Need a business card for new company. I have a logo already that I want to be built into the card and should use those colours

Company is called steered by tallies
Design must bring steered by tallies to life not be a card that could be for anyone with a logo put on it.

Like the front to be fairly clean and uncluttered bringing the logo out with a suitable design on the back of the card.

The logo represents a compass and business growth so those themes along with numbers, analytics , data are appropriate.
I'm often working with creative industries so also needs to reflect the creative side of analytics rather than be very corporate looking.

Target Market(s)

Ad agency, media agency, consumer goods clients

Industry/Entity Type

Market Research

Contact Information for Business Card

Needs to include name, title, email and phone number

Colors
f78f20
f68d4d
ec1f27

Requirements
Must have
• Must bring steered by tallies to life not be a card that could be for anyone with a logo put on it.
• Logo, Correct colours
• Like a design on the back that relates to company name
• Designs for both sides
Should not have
• Please do not just submit logo and a coloured card.
• It needs to have a design element to it
• No black background
• No clear cards - needs front & back

```html
<!DOCTYPE html>
<html lang="en">
<head>
<meta charset="utf-8">
<title>Steered by Tallies – Business Card</title>
<link href="https://fonts.googleapis.com/css2?family=Open+Sans:wght@400;600&display=swap" rel="stylesheet">
<style>
  :root {
    --backdrop: #6e6e71;
    --card-white: #f3f3f1;
    --card-red: #861318;
    --brand-orange: #f78f20;
    --brand-coral: #f68d4d;
    --brand-red: #ec1f27;
    --ink-grey: #5a5c60;
    --ink-white: #ffffff;
  }
  * { margin: 0; padding: 0; box-sizing: border-box; }
  html, body {
    width: 1200px;
    height: 913px;
    overflow: hidden;
    background: var(--backdrop);
    font-family: "Open Sans", Arial, sans-serif;
  }
  .canvas { position: relative; width: 1200px; height: 913px; }
  .card {
    position: absolute;
    overflow: hidden;
    box-shadow: 0 10px 28px rgba(0, 0, 0, 0.3);
  }

  /* Back of card: contact side */
  .card-back {
    left: 150px;
    top: 176px;
    width: 320px;
    height: 560px;
    background: var(--card-red);
    color: var(--ink-white);
    display: flex;
    flex-direction: column;
    align-items: center;
    padding-top: 70px;
    text-align: center;
  }
  .back-brand {
    display: flex;
    align-items: center;
    gap: 10px;
    font-size: 17px;
    color: var(--ink-white);
    margin-bottom: 56px;
  }
  .back-brand .brand-dot {
    width: 40px;
    height: 40px;
    border: 2px solid var(--ink-white);
    border-radius: 50%;
  }
  .contact-item {
    display: flex;
    flex-direction: column;
    align-items: center;
    margin-bottom: 14px;
  }
  .contact-item svg { width: 14px; height: 14px; margin-bottom: 5px; }
  .person-name {
    font-size: 17px;
    font-weight: 600;
    letter-spacing: 0.5px;
    color: var(--brand-orange);
    text-transform: uppercase;
  }
  .person-title { font-size: 13px; margin-top: 2px; margin-bottom: 10px; }
  .contact-text { font-size: 13px; }

  .growth-chart {
    position: absolute;
    left: 0;
    bottom: 0;
    width: 320px;
    height: 130px;
  }

  /* Front of card: brand side */
  .card-front {
    left: 540px;
    top: 296px;
    width: 560px;
    height: 320px;
    background: var(--card-white);
  }
  .front-brand {
    position: absolute;
    inset: 0;
    display: flex;
    align-items: center;
    justify-content: center;
    gap: 22px;
  }
  .front-brand .brand-dot {
    width: 88px;
    height: 88px;
    border: 3px solid var(--brand-orange);
    border-radius: 50%;
  }
  .brand-name {
    font-size: 40px;
    line-height: 1.05;
    color: var(--ink-grey);
  }
  .tally-strip {
    position: absolute;
    left: 0;
    bottom: 0;
    width: 560px;
    height: 46px;
  }
</style>
</head>
<body>
<main class="canvas">

  <section class="card card-back" aria-label="Card back">
    <div class="back-brand">
      <span class="brand-dot"></span>
      <span>Steered by Tallies</span>
    </div>

    <div class="contact-item">
      <svg viewBox="0 0 14 14" aria-hidden="true"><circle cx="7" cy="4" r="3" fill="var(--brand-orange)"/><path d="M1 14c0-4 3-6 6-6s6 2 6 6z" fill="var(--brand-orange)"/></svg>
      <span class="person-name">Alan Marsh</span>
      <span class="person-title">CEO/Founder</span>
    </div>

    <div class="contact-item">
      <svg viewBox="0 0 14 14" aria-hidden="true"><path d="M3 1l2 3-1.5 1.5c.8 2 2.5 3.7 4.5 4.5L9.5 8.5l3 2L11 13C5.5 12.5 1.5 8.5 1 3z" fill="var(--brand-orange)"/></svg>
      <span class="contact-text">555 014 2290</span>
    </div>

    <div class="contact-item">
      <svg viewBox="0 0 14 14" aria-hidden="true"><rect x="1" y="3" width="12" height="8" fill="var(--brand-orange)"/><path d="M1 3l6 5 6-5" stroke="var(--card-red)" stroke-width="1" fill="none"/></svg>
      <span class="contact-text">alan@steeredbytallies.com</span>
    </div>

    <div class="contact-item">
      <svg viewBox="0 0 14 14" aria-hidden="true"><circle cx="7" cy="7" r="6" fill="var(--brand-orange)"/><path d="M1 7h12M7 1c-3 3-3 9 0 12M7 1c3 3 3 9 0 12" stroke="var(--card-red)" stroke-width="0.9" fill="none"/></svg>
      <span class="contact-text">www.steeredbytallies.com</span>
    </div>

    <svg class="growth-chart" viewBox="0 0 320 130" aria-hidden="true">
      <g fill="var(--ink-white)" opacity="0.12">
        <rect x="28" y="98" width="22" height="32"/>
        <rect x="66" y="88" width="22" height="42"/>
        <rect x="104" y="92" width="22" height="38"/>
        <rect x="142" y="74" width="22" height="56"/>
        <rect x="180" y="62" width="22" height="68"/>
        <rect x="218" y="48" width="22" height="82"/>
        <rect x="256" y="30" width="22" height="100"/>
      </g>
      <polyline points="39,88 77,76 115,82 153,60 191,48 229,34 267,14"
                fill="none" stroke="var(--brand-orange)" stroke-width="2"/>
      <g fill="var(--brand-orange)">
        <circle cx="39" cy="88" r="3"/><circle cx="77" cy="76" r="3"/>
        <circle cx="115" cy="82" r="3"/><circle cx="153" cy="60" r="3"/>
        <circle cx="191" cy="48" r="3"/><circle cx="229" cy="34" r="3"/>
        <circle cx="267" cy="14" r="4" fill="var(--brand-red)"/>
      </g>
    </svg>
  </section>

  <section class="card card-front" aria-label="Card front">
    <div class="front-brand">
      <span class="brand-dot"></span>
      <span class="brand-name">Steered by<br>Tallies</span>
    </div>
    <svg class="tally-strip" viewBox="0 0 560 46" aria-hidden="true">
      <g stroke-width="3" stroke-linecap="round">
        <g stroke="var(--brand-orange)">
          <line x1="472" y1="14" x2="472" y2="34"/><line x1="480" y1="14" x2="480" y2="34"/>
          <line x1="488" y1="14" x2="488" y2="34"/><line x1="496" y1="14" x2="496" y2="34"/>
        </g>
        <line x1="466" y1="30" x2="502" y2="18" stroke="var(--brand-red)"/>
        <g stroke="var(--brand-coral)">
          <line x1="516" y1="14" x2="516" y2="34"/><line x1="524" y1="14" x2="524" y2="34"/>
        </g>
      </g>
      <rect x="0" y="42" width="380" height="4" fill="var(--brand-orange)"/>
      <rect x="380" y="42" width="100" height="4" fill="var(--brand-coral)"/>
      <rect x="480" y="42" width="80" height="4" fill="var(--brand-red)"/>
    </svg>
  </section>

</main>
</body>
</html>
```